Business Card Design for Property Development Company Director

I am looking for a professional and unforgettable business card design for our Director of our Property Development Company.
Please see attached .pptx file to find out what information to include. You don't have to follow the exact format shown in the file - I am interested to see your creative flair using the information provided.

```html
<!DOCTYPE html>
<html lang="en">
<head>
<meta charset="UTF-8">
<title>Harwick Property Group – Business Card</title>
<link href="https://fonts.googleapis.com/css2?family=Montserrat:wght@600;700&family=Open+Sans:wght@400;600&display=swap" rel="stylesheet">
<style>
  :root {
    --backdrop: #3a3b3e;
    --brand-blue: #1059a9;
    --brand-grey: #666769;
    --paper: #ffffff;
    --text-grey: #5a5b5e;
  }
  * { box-sizing: border-box; margin: 0; padding: 0; }
  html, body {
    width: 1200px; height: 900px; overflow: hidden;
    background: var(--backdrop);
    font-family: "Open Sans", Arial, sans-serif;
  }
  .stage { position: relative; width: 1200px; height: 900px; }

  .card {
    position: absolute;
    width: 580px; height: 330px;
    border-radius: 26px;
    overflow: hidden;
    box-shadow: 0 14px 30px rgba(0,0,0,0.45);
  }

  /* Front side */
  .card--front {
    left: 70px; top: 80px;
    background: var(--brand-blue);
    color: var(--paper);
    text-align: center;
  }
  .front__tagline {
    position: absolute; left: 0; right: 0; top: 58px;
    font-size: 17px; line-height: 1.5; letter-spacing: 0.2px;
  }
  .brand {
    display: flex; align-items: center; gap: 14px;
  }
  .brand__square {
    width: 30px; height: 30px; flex: none;
  }
  .brand__name {
    font-family: "Open Sans", Arial, sans-serif;
    font-weight: 600; font-size: 28px; letter-spacing: 0.5px;
    line-height: 1.05; text-align: left;
  }
  .card--front .brand {
    position: absolute; left: 0; right: 0; top: 140px;
    justify-content: center;
  }
  .card--front .brand__square { background: var(--paper); }
  .card--front .brand__name { color: var(--paper); }
  .front__invite {
    position: absolute; left: 0; right: 0; bottom: 48px;
    font-size: 14px; letter-spacing: 0.3px;
  }

  /* Back side */
  .card--back {
    left: 550px; top: 480px;
    background: var(--paper);
  }
  .card--back .brand {
    position: absolute; right: 40px; top: 36px;
  }
  .card--back .brand__square { background: var(--brand-blue); }
  .card--back .brand__name { color: var(--brand-blue); font-size: 25px; }

  .back__tab {
    position: absolute; left: 0; top: 150px;
    width: 22px; height: 44px; background: var(--brand-blue);
  }
  .person {
    position: absolute; left: 44px; top: 138px;
  }
  .person__name {
    font-family: "Montserrat", Arial, sans-serif;
    font-weight: 700; font-size: 24px; line-height: 32px;
    color: var(--brand-blue);
  }
  .person__role {
    font-size: 17px; line-height: 24px; color: var(--text-grey); margin-left: 4px;
  }
  .back__rule {
    position: absolute; left: 134px; right: 40px; top: 182px;
    height: 2px; background: var(--brand-blue);
  }
  .contact {
    position: absolute; left: 48px; top: 222px;
    list-style: none;
  }
  .contact__item {
    display: flex; align-items: center; gap: 10px;
    font-size: 14.5px; color: var(--text-grey); line-height: 22px;
  }
  .contact__icon { width: 13px; height: 13px; flex: none; }

  .licence {
    position: absolute; right: 40px; top: 206px;
    text-align: left; font-size: 14px; line-height: 1.3;
  }
  .licence__label { color: var(--brand-blue); }
  .licence__numbers { color: var(--text-grey); }

  .back__band {
    position: absolute; left: 0; bottom: 0; width: 580px; height: 46px;
  }
</style>
</head>
<body>
<main class="stage">

  <section class="card card--front" aria-label="Card front">
    <p class="front__tagline">Property Development &amp;<br>Site Acquisition Specialists</p>
    <div class="brand">
      <span class="brand__square"></span>
      <span class="brand__name">HARWICK<br>PROPERTY GROUP</span>
    </div>
    <p class="front__invite">Ask me about our INVESTMENT &amp; PARTNERSHIP opportunities</p>
  </section>

  <section class="card card--back" aria-label="Card back">
    <div class="brand">
      <span class="brand__square"></span>
      <span class="brand__name">HARWICK<br>PROPERTY GROUP</span>
    </div>

    <span class="back__tab"></span>

    <div class="person">
      <h1 class="person__name">Daniel Marsh</h1>
      <p class="person__role">Director</p>
    </div>

    <span class="back__rule"></span>

    <div class="licence">
      <p class="licence__label">Real Estate Lic:</p>
      <p class="licence__numbers">1234567 &amp; 1234568</p>
    </div>

    <ul class="contact">
      <li class="contact__item">
        <svg class="contact__icon" viewBox="0 0 24 24" aria-hidden="true"><path fill="#1059a9" d="M6.6 10.8a15.1 15.1 0 0 0 6.6 6.6l2.2-2.2a1 1 0 0 1 1-.25 11.4 11.4 0 0 0 3.6.57 1 1 0 0 1 1 1V20a1 1 0 0 1-1 1A17 17 0 0 1 3 4a1 1 0 0 1 1-1h3.5a1 1 0 0 1 1 1c0 1.25.2 2.45.57 3.57a1 1 0 0 1-.25 1z"/></svg>
        0400 123 456
      </li>
      <li class="contact__item">
        <svg class="contact__icon" viewBox="0 0 24 24" aria-hidden="true"><rect x="2" y="5" width="20" height="14" rx="1.5" fill="#1059a9"/><path d="M3 6l9 7 9-7" fill="none" stroke="#fff" stroke-width="2"/></svg>
        daniel@harwickgroup.com.au
      </li>
      <li class="contact__item">
        <svg class="contact__icon" viewBox="0 0 24 24" aria-hidden="true"><circle cx="12" cy="12" r="10" fill="#1059a9"/><path d="M2 12h20M12 2c3 3 3 17 0 20M12 2c-3 3-3 17 0 20" fill="none" stroke="#fff" stroke-width="1.5"/></svg>
        www.harwickgroup.com.au
      </li>
    </ul>

    <svg class="back__band" viewBox="0 0 580 46" preserveAspectRatio="none" aria-hidden="true">
      <polygon points="0,34 450,8 450,46 0,46" fill="#1059a9"/>
      <polygon points="458,8 580,0 580,46 458,46" fill="#666769"/>
    </svg>
  </section>

</main>
</body>
</html>
```